VFX Company Business Card Design Project

The Kestrel Works is a decentralized Visual Effects Studio servicing the television and feature film industries.
Project Brief:
Take our logo that was previously designed on Pencil Harbor and make a double sided business card.
Requirements:
- Card MUST be double sided.
- Front of card MUST have the yellow part of our logo against the dark grey background.
- Back of card is completely up to the designer.
- Back of card must include the complete company logo.
Please follow these File Preparation guidelines:
http://printnook.ca/infopage?file=filetype_en&s=PrintNook_new&lang=en
Business

```html
<!DOCTYPE html>
<html lang="en">
<head>
<meta charset="utf-8">
<title>The Kestrel Works – Business Card</title>
<link rel="stylesheet" href="https://fonts.googleapis.com/css2?family=Source+Sans+3:ital,wght@0,400;0,600;1,700&display=swap">
<style>
  :root {
    --backdrop: #d6ae86;
    --card: #262626;
    --panel: #5e6d70;
    --panel-rim: #eaf0e2;
    --ink-light: #f2f4ee;
    --ink-soft: #dfe5e0;
    --steel: #a9b3b2;
    --gold: #fcc42a;
    --label: #1a1a1a;
  }
  * { box-sizing: border-box; margin: 0; padding: 0; }
  html, body { width: 1200px; height: 788px; overflow: hidden; }
  body {
    position: relative;
    background: var(--backdrop);
    font-family: "Source Sans 3", "Myriad Pro", sans-serif;
  }
  .view-label {
    position: absolute;
    font-size: 22px;
    color: var(--label);
    transform: translateX(-50%);
  }
  .card {
    position: absolute;
    width: 524px;
    height: 300px;
    border-radius: 22px;
    background: var(--card);
    overflow: hidden;
    color: var(--ink-light);
  }
  .card--back { left: 338px; top: 78px; }
  .card--front-1 { left: 54px; top: 446px; }
  .card--front-2 { left: 622px; top: 446px; }

  .wordmark { position: absolute; left: 0; right: 0; text-align: center; }
  .wordmark__name {
    font-weight: 600;
    white-space: nowrap;
    line-height: 1;
  }
  .wordmark__tagline {
    color: var(--steel);
    letter-spacing: 5px;
    font-size: 16px;
    margin-top: 6px;
  }
  .card--back .wordmark { top: 32px; }
  .card--back .wordmark__name { font-size: 40px; color: var(--ink-light); }

  .contact-panel {
    position: absolute;
    left: 0; right: 0; top: 150px; bottom: 0;
    background: var(--panel);
    border-top: 5px solid var(--panel-rim);
  }

  .contact { position: absolute; left: 0; right: 0; top: 166px; text-align: center; }
  .contact__name { font-size: 21px; color: var(--ink-soft); line-height: 1.1; }
  .contact__role { font-size: 13px; color: var(--ink-soft); letter-spacing: 1px; }
  .contact__line { font-size: 14px; margin-top: 7px; }
  .contact__line b { font-style: italic; font-weight: 700; }
  .contact__sep { margin: 0 8px; }
  .contact__address { font-size: 13px; margin-top: 8px; }

  .front-name {
    position: absolute; left: 0; right: 0; text-align: center;
    font-weight: 600; color: var(--gold); line-height: 1;
  }
  .card--front-1 .front-name { top: 118px; font-size: 52px; }
  .card--front-2 .wordmark { top: 122px; }
  .card--front-2 .wordmark__name { font-size: 38px; color: var(--ink-light); }
  .card--front-2 .wordmark__tagline { font-size: 15px; }

  .site-url {
    position: absolute; left: 0; right: 0; bottom: 20px;
    text-align: center; font-size: 20px; letter-spacing: 4px;
    color: var(--ink-light);
  }
</style>
</head>
<body>
  <span class="view-label" style="left:600px; top:32px;">Back</span>
  <span class="view-label" style="left:327px; top:403px;">Front - 1</span>
  <span class="view-label" style="left:900px; top:403px;">Front - 2</span>

  <section class="card card--back">
    <div class="wordmark">
      <div class="wordmark__name">The Kestrel Works</div>
      <div class="wordmark__tagline">VIRTUAL STUDIO</div>
    </div>
    <div class="contact-panel" aria-hidden="true"></div>
    <div class="contact">
      <div class="contact__name">Your Name</div>
      <div class="contact__role">Designation</div>
      <div class="contact__line"><b>phone</b> 123-456-7890<span class="contact__sep">|</span><b>cell</b> 123-456-7890</div>
      <div class="contact__line"><b>email</b> info@website.com<span class="contact__sep">|</span><b>web</b> www.website.com</div>
      <div class="contact__address">0000#, Area Name, Street Name, State Name, Country code</div>
    </div>
  </section>

  <section class="card card--front-1">
    <div class="front-name">The Kestrel Works</div>
    <div class="site-url">www.website.com</div>
  </section>

  <section class="card card--front-2">
    <div class="wordmark">
      <div class="wordmark__name">The Kestrel Works</div>
      <div class="wordmark__tagline">VIRTUAL STUDIO</div>
    </div>
    <div class="site-url">www.website.com</div>
  </section>
</body>
</html>
```